Building Design company needing a letterhead

We need a letter head for our Building Design company to send letters etc. to our clients, consultants, councils etc. We would like to see our logo used and company colours. I have attached our style guide and an example of our current letterheads. Top left we would like our logo, top right we would like the company details and at the footer we would like some sort of image/design etc. that suits our brand. I like the Tarrow Design letterhead attached.

Target Market(s)

Professionals, Councils, Consultants, Mums & Dads

Industry/Entity Type

Architecture

Other font styles liked:
• refer the design style guide

Colors
f37122
000000
1b1b1b

Requirements
Must have
• Must have the minimum of a logo, company details and footer
Nice to have
• An image/design made for the footer that would suite our brand and website at www.corvanplans.com.au. Also it would be nice to include the KMEOT logo somewhere perhaps included in the footer.
Should not have
• Large images in the header. I just want the logo and company details.

```html
<!DOCTYPE html>
<html lang="en">
<head>
<meta charset="utf-8">
<title>Corvan Design Letterhead</title>
<link rel="stylesheet" href="https://fonts.googleapis.com/css2?family=Open+Sans:wght@400;600;700&display=swap">
<style>
  :root {
    --backdrop: #878787;
    --paper: #ffffff;
    --brand-orange: #e55a27;
    --ink: #1b1b1b;
    --rule: #dcdcdc;
    --watermark: #f1efee;
  }
  * { margin: 0; padding: 0; box-sizing: border-box; }
  html, body {
    width: 847px; height: 1200px; overflow: hidden;
    background: var(--backdrop);
    font-family: "Open Sans", Arial, sans-serif;
  }
  .letterhead {
    position: absolute; left: 70px; top: 70px;
    width: 707px; height: 1060px;
    background: var(--paper); overflow: hidden;
  }
  .sender { position: absolute; left: 20px; top: 45px; }
  .sender-name {
    color: var(--brand-orange); font-size: 12px; font-weight: 600;
    letter-spacing: 0.2px; line-height: 1.2;
  }
  .sender-role { color: var(--ink); font-size: 9px; line-height: 1.4; }
  .brand {
    position: absolute; left: 259px; top: 26px;
    display: flex; align-items: center; gap: 9px;
  }
  .brand-square { width: 24px; height: 24px; background: var(--brand-orange); }
  .brand-name {
    color: var(--ink); font-size: 24px; font-weight: 600;
    line-height: 1.05; letter-spacing: 1.5px;
  }
  .contact {
    position: absolute; right: 28px; top: 33px;
    list-style: none; text-align: right;
    color: var(--ink); font-size: 10px; line-height: 16.5px;
  }
  .contact li { display: flex; justify-content: flex-end; align-items: center; gap: 7px; }
  .contact svg { width: 8px; height: 8px; fill: var(--brand-orange); }
  .header-rule {
    position: absolute; left: 0; right: 0; top: 118px;
    border-top: 1px solid var(--rule);
  }
  .watermark {
    position: absolute; left: 84px; top: 330px; width: 540px;
    color: var(--watermark); font-weight: 600;
    font-size: 118px; line-height: 1.12; letter-spacing: 2px;
    white-space: nowrap; user-select: none;
  }
  .footer-band { position: absolute; left: 0; bottom: 0; width: 707px; height: 62px; }
  .footer-text {
    position: absolute; left: 0; right: 0; bottom: 0; height: 62px;
    text-align: center; color: #ffffff; font-size: 9.5px; line-height: 13px;
  }
  .footer-web { position: absolute; left: 0; right: 0; top: 16px; }
  .footer-address { position: absolute; left: 0; right: 0; top: 40px; }
</style>
</head>
<body>
  <main class="letterhead">
    <header>
      <div class="sender">
        <p class="sender-name">MARA QUINLAN</p>
        <p class="sender-role">Trial Attorney</p>
      </div>
      <div class="brand">
        <span class="brand-square"></span>
        <p class="brand-name">CORVAN<br>DESIGN</p>
      </div>
      <ul class="contact">
        <li>123-456-7890
          <svg viewBox="0 0 10 10"><path d="M1 4c0-2 8-2 8 0v1H7V4H3v1H1zM2 6h6l1 3H1z"/></svg></li>
        <li>123-456-7890
          <svg viewBox="0 0 10 10"><path d="M2 1h5v3H2zM1 4h8v5H1z"/></svg></li>
        <li>info@companyname.com
          <svg viewBox="0 0 10 10"><path d="M0 2h10v6H0zM1 3l4 3 4-3z" fill-rule="evenodd"/></svg></li>
      </ul>
      <div class="header-rule"></div>
    </header>

    <div class="watermark" aria-hidden="true">CORVAN<br>DESIGN</div>

    <footer>
      <svg class="footer-band" viewBox="0 0 707 62" preserveAspectRatio="none">
        <path d="M0 62 Q353 -62 707 62 Z" fill="var(--brand-orange)"/>
      </svg>
      <div class="footer-text">
        <p class="footer-web">www.copanyname.com</p>
        <p class="footer-address">Address Line1, Addres Line2 Country -123456</p>
      </div>
    </footer>
  </main>
</body>
</html>
```